BRIVAN 2026 Flyer for Conference

BRIVAN needs a design for a 1-page flyer that we will hand out at an upcoming event & then later post online as a pdf. There are 3 elements which need to be on the flyer:

1) A logo. This should be prominent on the design (e.g., in the middle). The flyer should use the colors that are in that logo (e.g., for accents, design elements, and/or text; not all of these have to be used):
Dark blue: #185577
Med blue: #327C9A
Teal: #4EB1C2
Light Teal: #9EDBE6

2) The conference theme -- Oceans of Knowledge: Diving into Information Literacy -- should be at the flyer's top.

3) Finally, these six tracks should be listed below the theme and the logo (it's font size should be at least a couple sizes smaller than the size used for the theme):
- Pearls of Pedagogy: Teaching Techniques that Work
- The Depth Gauge: Measuring Instructional Impact
- Techtonic Shifts: Innovation and Educational Technology
- Captain's Log: Navigating Leadership in Library Instruction
- Swimming Together: Collaborating with Others
- The Bermuda Triangle: Exploring (Seemingly) Eternal Challenges

Font styles to use
Sans Serif

Colors
0094D4
00A9DD
6FCCEA
C7EBF8
E9F6FB

Requirements
Must have
• The 3 elements listed in the description: 1) the logo, 2) the text of the theme and 3) the text for the tracks.

```html
<!DOCTYPE html>
<html lang="en">
<head>
<meta charset="utf-8">
<title>BRIVAN 2026 – Oceans of Knowledge</title>
<link href="https://fonts.googleapis.com/css2?family=Poppins:wght@400;600;700;800&display=swap" rel="stylesheet">
<style>
  :root{
    --brand-dark:#185577;
    --blue-strong:#0094D4;
    --blue-bright:#00A9DD;
    --blue-soft:#6FCCEA;
    --blue-pale:#C7EBF8;
    --blue-mist:#E9F6FB;
    --title-blue:#1E8FD2;
    --footer-blue:#1A8FD6;
    --ink:#222b33;
    --white:#ffffff;
  }
  *{box-sizing:border-box;margin:0;padding:0}
  html,body{width:927px;height:1200px;overflow:hidden;background:var(--white)}
  body{font-family:'Poppins',sans-serif;color:var(--ink)}
  .flyer{position:relative;width:927px;height:1200px;overflow:hidden;background:linear-gradient(180deg,var(--blue-mist) 0%,var(--white) 55%,var(--blue-pale) 100%)}
  .hero-photo{position:absolute;left:0;top:0;width:927px;height:640px;
    background:linear-gradient(100deg,#0b0b0d 0%,#231c17 30%,#6a5443 55%,#9c8977 75%,#7a6a5c 100%)}
  .waves{position:absolute;left:0;top:0}
  .brand-tab{position:absolute;left:364px;top:-30px;width:198px;height:200px;background:var(--white);
    border-radius:0 0 99px 99px;display:flex;align-items:center;justify-content:center;gap:8px;padding-top:30px}
  .brand-tab .dot{width:14px;height:14px;border-radius:50%;background:var(--blue-bright)}
  .brand-name{font-weight:800;color:var(--brand-dark);font-size:30px;line-height:1.05;text-align:center}
  .theme{position:absolute;left:24px;top:180px;color:var(--white)}
  .theme h1{font-weight:800;font-size:66px;line-height:60px;letter-spacing:0.5px}
  .theme p{font-weight:700;font-size:24.5px;margin-top:20px}
  .tracks{position:absolute;left:24px;top:643px;width:878px;display:grid;grid-template-columns:427px 427px;column-gap:24px;row-gap:20px}
  .track{position:relative;height:128px;background:var(--white);border-radius:64px;box-shadow:0 2px 10px rgba(0,148,212,.08)}
  .track .icon{position:absolute;top:7px;width:114px;height:114px;border-radius:50%;background:var(--title-blue);
    display:flex;align-items:center;justify-content:center}
  .track.left .icon{right:6px}
  .track.right .icon{left:9px}
  .track .text{position:absolute;top:0;height:128px;display:flex;flex-direction:column;justify-content:center}
  .track.left .text{right:140px;text-align:right;width:275px}
  .track.right .text{left:144px;width:275px}
  .track h2{font-weight:700;font-size:21.5px;color:var(--title-blue);line-height:1.25}
  .track p{font-size:15.5px;line-height:22px;margin-top:9px;color:var(--ink)}
  .footer{position:absolute;left:0;top:1103px;width:927px;height:97px;background:var(--footer-blue);color:var(--white)}
  .footer .badge{position:absolute;top:29px;width:46px;height:46px;border-radius:50%;background:rgba(255,255,255,.18);
    display:flex;align-items:center;justify-content:center}
  .phone{position:absolute;left:103px;top:22px}
  .phone strong{display:block;font-weight:700;font-size:28px;line-height:32px;letter-spacing:.5px}
  .phone span{font-size:13.5px}
  .contact{position:absolute;left:438px;top:24px}
  .contact strong{display:block;font-weight:700;font-size:20px;line-height:24px}
  .contact span{font-size:17px;white-space:nowrap}
</style>
</head>
<body>
<main class="flyer">
  <div class="hero-photo" role="img" aria-label="Photo of a young woman reading an open book beside library shelves"></div>

  <svg class="waves" width="927" height="1200" viewBox="0 0 927 1200" aria-hidden="true">
    <defs>
      <linearGradient id="mist" x1="0" y1="0" x2="0" y2="1">
        <stop offset="0.35" stop-color="#CFEEFA"/>
        <stop offset="0.6" stop-color="#EEF8FC"/>
        <stop offset="1" stop-color="#C7EBF8"/>
      </linearGradient>
    </defs>
    <path d="M0,345 C110,470 200,545 330,548 C470,550 560,455 700,462 C800,468 880,560 927,610 L927,1200 L0,1200Z" fill="#ffffff"/>
    <path d="M0,365 C110,495 200,570 330,573 C470,575 560,478 700,484 C800,490 880,585 927,640 L927,1200 L0,1200Z" fill="var(--blue-bright)"/>
    <path d="M0,440 C110,545 200,600 330,603 C470,605 560,500 700,505 C800,510 880,620 927,700 L927,1200 L0,1200Z" fill="var(--blue-strong)"/>
    <path d="M0,460 C110,560 200,612 330,612 C470,612 560,520 700,528 C800,534 880,640 927,720 L927,1200 L0,1200Z" fill="url(#mist)"/>
  </svg>

  <div class="brand-tab">
    <span class="dot"></span>
    <span class="brand-name">BRIVAN<br>2026</span>
  </div>

  <header class="theme">
    <h1>Oceans of<br>Knowledge</h1>
    <p>Diving into Information Literacy</p>
  </header>

  <section class="tracks">
    <article class="track left">
      <div class="text"><h2>Pearls of Pedagogy</h2><p>Teaching Techniques that Work</p></div>
      <div class="icon"><svg width="60" height="60" viewBox="0 0 60 60" fill="none" stroke="#fff" stroke-width="2.2" stroke-linecap="round"><rect x="22" y="6" width="32" height="22" rx="1"/><path d="M28 14h10M28 20h18M17 28a7 7 0 1 0 0.1 0M6 56v-8a11 11 0 0 1 22 0v8M28 40l14-12"/></svg></div>
    </article>
    <article class="track right">
      <div class="icon"><svg width="62" height="62" viewBox="0 0 62 62" fill="none" stroke="#fff" stroke-width="2.2" stroke-linecap="round"><rect x="6" y="10" width="50" height="36" rx="2"/><path d="M24 46v8M38 46v8M18 56h26M16 40V20M24 40V14M32 40V22M40 40V16M48 40V24M10 40h42"/></svg></div>
      <div class="text"><h2>Captain's Log</h2><p>Navigating Leadership in Library Instruction</p></div>
    </article>
    <article class="track left">
      <div class="text"><h2>The Depth Gauge</h2><p>Measuring Instructional Impact</p></div>
      <div class="icon"><svg width="62" height="62" viewBox="0 0 62 62" fill="none" stroke="#fff" stroke-width="2.4" stroke-linecap="round"><path d="M12 50a24 24 0 1 1 38 0"/><path d="M18 44a16 16 0 1 1 26 0"/><circle cx="31" cy="36" r="4"/><path d="M34 33l12-10"/></svg></div>
    </article>
    <article class="track right">
      <div class="icon"><svg width="62" height="62" viewBox="0 0 62 62" fill="none" stroke="#fff" stroke-width="2.2" stroke-linecap="round"><rect x="24" y="6" width="14" height="8" rx="1"/><path d="M24 14v18l7 6 7-6V14M8 42l12 12M54 42L42 54M20 54l8-10M42 54l-8-10"/><circle cx="31" cy="34" r="20" stroke-dasharray="2 4"/></svg></div>
      <div class="text"><h2>Swimming Together</h2><p>Collaborating with Others</p></div>
    </article>
    <article class="track left">
      <div class="text"><h2>Techtonic Shifts</h2><p>Innovation and Educational Technology</p></div>
      <div class="icon"><svg width="62" height="62" viewBox="0 0 62 62" fill="none" stroke="#fff" stroke-width="2.2" stroke-linecap="round"><path d="M6 22h18a7 7 0 0 1 7 7v27a7 7 0 0 0-7-7H6zM56 22H38a7 7 0 0 0-7 7v27a7 7 0 0 1 7-7h18z"/><circle cx="31" cy="14" r="6"/><path d="M31 2v3M21 8l2 2M41 8l-2 2M11 30h12M11 36h12M39 30h12M39 36h12"/></svg></div>
    </article>
    <article class="track right">
      <div class="icon"><svg width="62" height="62" viewBox="0 0 62 62" fill="none" stroke="#fff" stroke-width="2.2" stroke-linecap="round"><circle cx="50" cy="10" r="3"/><circle cx="38" cy="54" r="3"/><circle cx="10" cy="20" r="3"/><path d="M49 13l-10 38M13 21l14 6M28 16l6 6 8-4-6 8"/><path d="M12 44h20l-3 8H15z"/><path d="M18 44v-6h8v6"/></svg></div>
      <div class="text"><h2>The Bermuda Triangle</h2><p>Exploring (Seemingly) Eternal Challenges</p></div>
    </article>
  </section>

  <footer class="footer">
    <div class="badge" style="left:43px"><svg width="22" height="22" viewBox="0 0 22 22" fill="#fff"><path d="M1 5l6-2v14l-6 2zM8 3l6 2v14l-6-2zM15 5l6-2v14l-6 2z"/></svg></div>
    <div class="phone"><strong>+1 555-014-2026</strong><span>www.brivanevents.org</span></div>
    <div class="badge" style="left:379px"><svg width="22" height="22" viewBox="0 0 22 22" fill="#fff"><path d="M1 5l6-2v14l-6 2zM8 3l6 2v14l-6-2zM15 5l6-2v14l-6 2z"/></svg></div>
    <div class="contact"><strong>Contact Info</strong><span>48 Harbor Lane Suite 210, Lakemont 00000, United States</span></div>
  </footer>
</main>
</body>
</html>
```